Visitenkarten-Design für Steuerberater und Wirtschaftsprüfer
Thank you so much! Great communication, very fast and nice contact!
Zielgruppe
Steuerberater, Wirtschaftsprüfer in München
Aufgabenstellung
Wir haben ein Logo das uns gefällt, jetzt allerdings steht die Umfirmierung vor der Tür und aus der Kanzlei Zelliger (so unser Name) wird Zelliger und Partner mbB (die Jugend kommt mit als Partner in die Kanzlei) , Steuerberater, Wirtschaftsprüfer
Analog unseres alten Briefpapiers und der alten Visitenkarten soll eigentlich nur der Zusatz 'und Partner mbB' oder '& Partner mbB' gestaltet werden.
Das Dateiformat bei Visitenkarten bitte so übergeben, dass wir Namen selbst austauschen mit gängigen Officeprogrammen austauschen können. Bei den Visitenkarten ist das große 'Zelliger' geprägt.
Ich stelle das Logo, das aktuelle Briefpapier und aktuelle Visitenkarten ein. Unsere Farbe ist grau.
Das Logo bitte in .pdf, .png, .psd und .eps (sagt mi alles nichts, haben wir aber alles schon mal irgendwo gebraucht) , Visiten karten auch in .pddf und .ai
Bei Fragen kontaktiert mich gern jederzeit.

```html
<!DOCTYPE html>
<html lang="de">
<head>
<meta charset="utf-8">
<title>Zelliger &amp; Partner mbB – Briefbogen</title>
<link rel="stylesheet" href="https://fonts.googleapis.com/css2?family=Arimo:wght@400;700&family=Tinos&display=swap">
<style>
  :root {
    --backdrop: #1c1c1c;
    --paper: #ffffff;
    --ink: #111111;
    --brand-grey: #5e5e5e;
    --footer-grey: #808080;
    --spec-red: #d3222a;
    --dot-grey: #9a9a9a;
  }
  * { margin: 0; padding: 0; box-sizing: border-box; }
  html, body { width: 1101px; height: 1200px; overflow: hidden; background: var(--backdrop); }
  body { position: relative; font-family: "Arimo", Arial, sans-serif; color: var(--ink); }

  .sheet { position: absolute; left: 147px; top: 38px; width: 804px; height: 1125px; background: var(--paper); }
  .abs { position: absolute; white-space: nowrap; }

  .brand { position: absolute; left: 0; width: 804px; top: 36px; text-align: center; color: var(--brand-grey); font-weight: 400; }
  .brand-name { font-size: 40px; letter-spacing: 3px; line-height: 42px; }
  .brand-suffix { font-size: 15px; letter-spacing: 5px; line-height: 18px; }
  .brand-tagline { font-size: 11px; letter-spacing: 0.5px; line-height: 15px; }

  .sender-line { left: 96px; top: 190px; font-size: 7px; color: var(--brand-grey); }
  .sender-line b { font-weight: 700; }

  .address { left: 96px; top: 206px; font-size: 14.5px; line-height: 19px; }
  .date { right: 95px; top: 343px; font-size: 14.5px; line-height: 19px; }
  .subject { left: 96px; top: 378px; font-size: 18.5px; font-weight: 700; line-height: 22px; }
  .body-text { left: 96px; font-size: 14.5px; line-height: 19px; }

  .footer-rule { position: absolute; left: 93px; top: 1049px; width: 648px; height: 3px; background: var(--brand-grey); }
  .footer { position: absolute; left: 0; width: 804px; top: 1067px; text-align: center; font-size: 11px; line-height: 15px; color: var(--footer-grey); }
  .footer b { color: #5a5a5a; font-weight: 700; }

  .spec { position: absolute; color: var(--spec-red); font-family: "Tinos", "Times New Roman", serif; font-size: 15.5px; line-height: 19.5px; white-space: nowrap; }
  .spec-lines { position: absolute; left: 0; top: 0; }
  .margin-dot { position: absolute; width: 3px; height: 3px; border-radius: 50%; background: var(--dot-grey); }
</style>
</head>
<body>
  <main class="sheet">
    <header class="brand">
      <div class="brand-name">ZELLIGER</div>
      <div class="brand-suffix">&amp; PARTNER mbB</div>
      <div class="brand-tagline">STEUERBERATER | WIRTSCHAFTSPRÜFER</div>
    </header>

    <p class="abs sender-line"><b>KANZLEI ANTON R. ZELLIGER</b> | Lindenhofstr. 22 | 80331 München</p>

    <address class="abs address" style="font-style:normal">
      Musterfirma<br>Max Mustermann<br>Adresszusatz<br>Musterstraße 123<br>12345 Musterstadt<br>Musterland
    </address>

    <p class="abs date">München, 00. Monat 2014</p>
    <h1 class="abs subject">Betreffzeile</h1>

    <p class="abs body-text" style="top:438px">Sehr geehrter Herr Mustermann,</p>
    <p class="abs body-text" style="top:476px">Kurzer Brief an ein Idol. Lieber Onkel Gerold, schon lange wollte ich Dir sagen, daß ich<br>Dich für einen ganz tollen Texter halte. Ich weiß, Du hörst sehr gerne Lob, und deshalb kann<br>man nicht oft genug sagen, daß Du der Größte bist.</p>
    <p class="abs body-text" style="top:551px">Gerade in Deinem Alter ist man ja gesegnet, wenn man noch so witzig schreiben kann wie<br>Du. Viele Deiner Werberkollegen sind ja schon zu wichtig, um noch den Humor zu haben.</p>
    <p class="abs body-text" style="top:608px">Du bist da ganz anders. Du kannst richtig komisch sein. Und das, obwohl Du in Deinem sehr<br>langen Leben auch schon sehr viele unangenehme Dinge schreiben mußtest. Texte<br>für Burgerhaus zum Beispiel. Oder kleine Reime für Onkel Wilfried. Nein, Du hast es wirklich<br>nicht leicht gehabt. Und dann noch die Selbstdarstellung für Tante Ilse.</p>
    <p class="abs body-text" style="top:702px">Gerade in Deinem Alter ist man ja gesegnet, wenn man noch so witzig schreiben kann wie<br>Du. Viele Deiner Werberkollegen sind ja schon zu wichtig, um noch den Humor zu haben.</p>
    <p class="abs body-text" style="top:778px">Mit freundlichen Grüßen</p>
    <p class="abs body-text" style="top:854px">Vorname Name<br>Titel</p>

    <div class="footer-rule"></div>
    <footer class="footer">
      <div><b>KANZLEI ANTON R. ZELLIGER</b> | Lindenhofstr. 22 | 80331 München</div>
      <div><b>fon</b> 089-41207733 | <b>fax</b> 089-41207734 | <b>mail</b> info@kanzlei-zelliger.com | <b>web</b> www.kanzlei-zelliger.com</div>
      <div><b>UstID</b> DE 204815937 | <b>IBAN</b> DE 12 3456 7800 0012 3456 78 | <b>BIC</b> BANKDEFFXXX</div>
    </footer>
  </main>

  <div class="margin-dot" style="left:167px;top:408px"></div>
  <div class="margin-dot" style="left:167px;top:605px"></div>

  <svg class="spec-lines" width="1101" height="1200" aria-hidden="true">
    <g stroke="#d3222a" stroke-width="1" fill="none">
      <line x1="243.5" y1="150" x2="243.5" y2="248"/>
      <line x1="147" y1="248.5" x2="243" y2="248.5"/>
      <line x1="857" y1="248.5" x2="951" y2="248.5"/>
      <line x1="147" y1="703.5" x2="243" y2="703.5"/>
      <line x1="857" y1="703.5" x2="951" y2="703.5"/>
      <line x1="384" y1="301.5" x2="453" y2="301.5"/>
      <line x1="681.5" y1="798" x2="681.5" y2="868"/>
    </g>
    <g fill="#d3222a">
      <polygon points="376,301.5 386,297.5 386,305.5"/>
      <polygon points="681.5,790 677.5,800 685.5,800"/>
    </g>
  </svg>

  <div class="spec" style="left:251px;top:161px">55 mm</div>
  <div class="spec" style="left:171px;top:227px">25 mm</div>
  <div class="spec" style="left:880px;top:227px">25 mm</div>
  <div class="spec" style="left:171px;top:682px">25 mm</div>
  <div class="spec" style="left:880px;top:682px">25 mm</div>
  <div class="spec" style="left:458px;top:283px">Anschriftenfeld:<br>75mm breit, 30mm hoch<br>Schrift: Arial, 11pt, 6 mögliche<br>Zeilen</div>
  <div class="spec" style="left:682px;top:876px">Textfeld:<br>160mm breit,180mm hoch<br>Schrift: Arial, 11pt (Betreff 14pt bold)</div>
</body>
</html>
```